San Francisco Leading Consulting firm - 47Vora Web Design Project

•Create a Web Design
•Uncoded webpage layout design
•2 Pages Design - Homepage + Interior Page

Task Description
Hello, we're looking for a re-design our current website www.47vora-example.com

we have a sample mockup design @

http://47vora.pubtrellis-example.org/

This shows the layout that we like and also a sample of 6 pictures that would change based on where you mouse over..

6 pictures HOME design needs to be included.

SMART
THOUGHTFUL
FLEXIBLE
CREATIVE SERVICES
TECHNICAL SERVICES
PARTNERS

sites we like:

http://www.melvanadvisory-example.com/Home.cfm?id=Home
http://www.plinthworks-example.com/index.html

Our company can be best described as: 100+ employees, cutting-edge, depandable, innovative, strong, smart.

Our Primary focus is: IT Consulting Services and Creative Design services

47Vora LLC is a consulting firm providing creative design, business and technology solutions to both private and public interests.

Established in 1996, 47Vora is a San Francisco based company providing specialists for a range of business needs including:

Creative Design Services
•Print
•Logo Design
•Website Design
•Illustration

and

Business and Technology solutions

•Application Software and Web Development
•Business Process Re-Design (BPR)
•Business/Systems Analysis and Requirement Documentation
•Mentoring and Training
•Network/Hardware Installation Services
•System Design and Architecture
•Vendor Management
•Docuvault Architecture and Implementation

our sample mockup site:

Reason: Due to holiday season, we're not available to work with designers and finilize our design.  

Thank you very much for submitting your design.

We appreciate your time and creativity.   Since, our office is currently closed for holidays, we will be reviewing it in details next week and will make our decision as soon as possible.

It would be great if you could submit any of your changes by Wed next week, so it would be part of our reviews. 

Please see updated wireframe under attachments:  we have some minor updates to our wireframe that we would like you to update your designs, if possible.  

We also encorouge you not to use our standard wireframe and come up with more unique designs.   Everything would be considered when we review your design.

 

Target Market(s)

Creative services and professional services clients, including government agencies

Industry/Entity Type

Business

Requirements
Must have
• Clean, professional look, easy navigation

```html
<!DOCTYPE html>
<html lang="en">
<head>
<meta charset="utf-8">
<title>47Vora — Home</title>
<link href="https://fonts.googleapis.com/css2?family=Arimo:wght@400;700&family=Questrial&display=swap" rel="stylesheet">
<style>
:root{
  --ink:#1b1b1b;
  --dark:#1a1c1e;
  --darker:#0c0d0e;
  --panel:#141517;
  --accent:#1f3fd6;
  --sky:#2aa6ef;
  --sky-deep:#1d7fe0;
  --rule:#d9dde0;
  --muted:#333;
  --foot-text:#c9c9c9;
  --white:#fff;
}
*{box-sizing:border-box;margin:0;padding:0}
html,body{width:1118px;height:1200px;overflow:hidden;background:#fff}
body{font-family:"Arimo",Arial,sans-serif;color:var(--ink)}
.page{position:absolute;left:0;top:0;width:1200px;height:1288px;transform:scale(.9317);transform-origin:0 0}
.abs{position:absolute}

/* header */
.header{left:97px;top:0;width:1007px;height:135px;background:linear-gradient(100deg,#cfcfcf 0%,#efefef 40%,#d9d9d9 70%,#f4f4f4 100%)}
.header-curve{left:97px;top:0;width:1007px;height:135px}
.brand{left:110px;top:30px;display:flex;align-items:center;gap:14px}
.brand-dot{width:64px;height:64px;border-radius:50%;background:var(--sky)}
.brand-name{font-family:"Questrial",sans-serif;font-size:46px;letter-spacing:3px;color:#2b2b2b}
.nav{left:471px;top:95px;width:633px;height:40px;background:var(--dark);display:flex;align-items:center;padding-left:26px}
.nav a{color:var(--white);text-decoration:none;font-size:14px}
.nav .sep{color:var(--white);font-size:14px;margin:0 20px}

/* hero */
.hero{left:97px;top:135px;width:1007px;height:388px;background:var(--dark)}
.hero-visual{left:110px;top:147px;width:697px;height:363px;background:radial-gradient(circle at 55% 45%,#7dff6a 0%,#2bb34a 18%,#2a3fbf 45%,#18206a 80%,#0d1240 100%)}
.hero-caption{left:183px;top:392px;font-size:26px;color:var(--white);text-shadow:0 0 3px #000}
.hero-panel{left:818px;top:147px;width:272px;height:295px;background:var(--panel)}
.hero-inner{left:824px;top:167px;width:260px;height:265px;background:#0e0f10;border:1px solid #2a2c2e}
.hero-title{left:834px;top:167px;width:250px;height:31px;background:linear-gradient(90deg,#2e3032,#0e0f10);color:var(--white);font-size:20px;padding:5px 9px}
.hero-text{left:838px;top:215px;width:234px;font-size:12px;line-height:20px;color:var(--white);text-align:justify}
.readmore{left:997px;top:402px;width:80px;height:25px;background:#3a3c3e;color:var(--white);font-size:13px;text-align:center;line-height:25px}
.hero-arrows{left:818px;top:452px;width:275px;height:56px;background:linear-gradient(90deg,#2a2c2e,#1b1d1f 50%,#3a3c3e)}
.arrow-box{left:824px;top:459px;width:38px;height:38px;background:#111}

/* content */
.content{left:97px;top:523px;width:1007px;height:524px;background:linear-gradient(#eaeff2,#ffffff)}
.col-head{font-size:16px;color:var(--ink);font-weight:400}
.col-head span{color:var(--accent)}
.col-rule{height:1px;background:var(--rule)}
.client-card{left:122px;top:593px;width:285px;height:173px;background:var(--white);border:1px solid #d4d4d4;display:flex;align-items:center;justify-content:center;gap:10px}
.client-mark{width:22px;height:22px;background:#3b3f7a}
.client-name{font-size:28px;font-weight:700;color:#3b3f7a}
.body-copy{font-size:12px;line-height:18px;color:var(--muted);text-align:justify}
.partner-copy{font-size:11.5px;letter-spacing:-.1px;line-height:20px}
.btn-dark{background:#000;color:var(--white);font-size:12px;border-radius:3px;text-align:center;line-height:22px;height:22px}
.services{left:455px;top:591px;width:290px;list-style:none}
.services li{font-size:12px;color:var(--muted);padding:0 0 0 11px;position:relative;margin-bottom:10px;line-height:20px}
.services li span{border-bottom:1px dotted #888;padding-bottom:1px;display:inline-block}
.services li::before{content:"";position:absolute;left:2px;top:7px;border-left:4px solid #333;border-top:3px solid transparent;border-bottom:3px solid transparent}
.services li.active{color:var(--accent)}
.partner-img{left:782px;top:595px;width:107px;height:107px;background:linear-gradient(135deg,#c9f0f5,#b08a6a 50%,#e3c6ad);border:2px solid #9ee3ec}

/* graphic designers */
.gd{left:121px;top:936px;width:951px;height:155px;border:1px solid #0d4fa0;border-radius:4px;background:linear-gradient(#1e8be6,#37b3f4 45%,#1a73d8);display:flex;overflow:hidden}
.gd-cell{position:relative;border-right:1px solid #d8ecff}
.gd-cell:last-child{border-right:0}
.gd-title{font-size:18px;color:var(--white);text-align:center;padding-top:8px;height:41px;border-bottom:1px solid #e6f3ff;margin:0 10px}
.gd-art{position:absolute;top:52px;left:50%;transform:translateX(-50%);width:72px;height:72px;border-radius:8px;opacity:.9}
.more{position:absolute;bottom:5px;right:15px;width:56px;height:18px;background:var(--white);border-radius:2px;font-size:11px;color:var(--sky-deep);line-height:18px;padding-left:5px}
.more::after{content:"»";position:absolute;right:0;top:0;width:20px;border-left:1px solid #9ccff5;text-align:center}

/* footer */
.footer{left:97px;top:1047px;width:1007px;height:241px;background:var(--darker)}
.foot-head{font-size:12px;color:var(--white)}
.foot-rule{height:1px;border-top:1px dotted #333}
.foot-list{list-style:none;font-size:11px;color:var(--foot-text)}
.foot-list li{height:24px}
.foot-list.links li::before{content:"»";margin-right:8px;color:#888}
.soc{display:flex;align-items:center;gap:6px;height:20px;font-size:11px;color:var(--foot-text)}
.soc i{width:14px;height:14px;background:#4a78c2;display:block}
.foot-divider{left:927px;top:1120px;width:1px;height:145px;background:#222}
.foot-brand{left:945px;top:1180px;display:flex;align-items:center;gap:8px}
.foot-brand i{width:22px;height:22px;border-radius:50%;background:var(--sky);display:block}
.foot-brand span{font-family:"Questrial",sans-serif;font-size:22px;letter-spacing:3px;color:#cfd6dc}
</style>
</head>
<body>
<div class="page">

  <header>
    <div class="abs header"></div>
    <svg class="abs header-curve" viewBox="0 0 1007 135" aria-hidden="true">
      <path d="M0 120 C300 60 600 50 1007 60" fill="none" stroke="#ffffff" stroke-width="14" opacity=".6"/>
      <path d="M880 135 C880 60 930 10 1007 0 L1007 135 Z" fill="#f6f6f6" opacity=".7"/>
    </svg>
    <div class="abs brand"><span class="brand-dot"></span><span class="brand-name">47VORA</span></div>
    <nav class="abs nav">
      <a href="#">Copmany</a><span class="sep">|</span>
      <a href="#">Technical Services</a><span class="sep">|</span>
      <a href="#">Creative Services</a><span class="sep">|</span>
      <a href="#">Partners</a><span class="sep">|</span>
      <a href="#">Contact Us</a>
    </nav>
  </header>

  <section>
    <div class="abs hero"></div>
    <div class="abs hero-visual" role="img" aria-label="Photo of a hand bending a flexible LED panel over glowing green and blue light rays"></div>
    <div class="abs hero-caption">Flexiblke</div>
    <div class="abs hero-panel"></div>
    <div class="abs hero-inner"></div>
    <div class="abs hero-title">FLEXIBLE</div>
    <p class="abs hero-text">Lorem Ipsum is simply dummy text of the printing and typesetting industry. Lorem Ipsum has been the industry's standard dummy text ever since the 1500s, when an unknown printer took a galley of type and scrambled it to make a type specimen book.</p>
    <div class="abs readmore">readmore</div>
    <div class="abs hero-arrows"></div>
    <div class="abs arrow-box"></div>
    <svg class="abs" style="left:830px;top:464px" width="24" height="28" viewBox="0 0 24 28" aria-hidden="true"><path d="M17 3 L6 14 L17 25" fill="none" stroke="#fff" stroke-width="4"/></svg>
    <svg class="abs" style="left:1060px;top:464px" width="24" height="28" viewBox="0 0 24 28" aria-hidden="true"><path d="M6 3 L17 14 L6 25" fill="none" stroke="#fff" stroke-width="4"/></svg>
  </section>

  <main>
    <div class="abs content"></div>

    <h2 class="abs col-head" style="left:137px;top:551px">Our <span>Clients</span></h2>
    <div class="abs col-rule" style="left:122px;top:582px;width:284px"></div>
    <div class="abs client-card"><span class="client-mark"></span><span class="client-name">Nimbrel</span></div>
    <p class="abs body-copy" style="left:125px;top:773px;width:278px">Lorem Ipsum is simply dummy text of the printing and typesetting industry. Lorem Ipsum has been the industry's standard dummy text ever since the 1500s, when an unknown printer took a galley of type and scrambled it to specimen book.</p>
    <div class="abs btn-dark" style="left:127px;top:872px;width:69px">View all</div>

    <h2 class="abs col-head" style="left:460px;top:555px">Our <span>Services</span></h2>
    <div class="abs col-rule" style="left:458px;top:582px;width:282px"></div>
    <ul class="abs services">
      <li class="active"><span>Business and Technology solutions</span></li>
      <li><span>Application Software and Web Development</span></li>
      <li><span>Business Process Re-Design (BPR)</span></li>
      <li><span style="width:258px">Business/Systems Analysis and Requirement Documentation</span></li>
      <li><span>Mentoring and Training</span></li>
      <li><span>Business and Technology solutions</span></li>
      <li><span>Business and Technology solutions</span></li>
      <li><span>Vendor Management</span></li>
      <li><span>Docuvault Architecture and Implementation</span></li>
    </ul>

    <h2 class="abs col-head" style="left:782px;top:555px">For <span>partners</span></h2>
    <div class="abs col-rule" style="left:780px;top:582px;width:292px"></div>
    <div class="abs partner-img" role="img" aria-label="Photo of four hands gripping each other's wrists in a square"></div>
    <p class="abs body-copy partner-copy" style="left:895px;top:590px;width:177px">Lorem Ipsum is simply dummy text of the printing and typeset-ting industry. Lorem Ipsum has been the industry's standard dummy text ever since the 1500s, when an unknown</p>
    <p class="abs body-copy partner-copy" style="left:784px;top:707px;width:288px">Lorem Ipsum is simply dummy text of the printing and typesetting industry. Lorem Ipsum has been the industry's standard dummy text ever since the 1500s, when an unknown printer took a galley of type and scrambled it to make a type specimen book. It has survived not only five centuries, but alsounchanged. It was popularised in the 1960sns of Lorem Ipsum.</p>
    <div class="abs btn-dark" style="left:1002px;top:872px;width:69px">Read More</div>

    <h2 class="abs col-head" style="left:123px;top:910px">For <span>graphic designers</span></h2>
  </main>

  <footer>
    <div class="abs footer"></div>

    <div class="abs foot-head" style="left:133px;top:1114px">Quick Linka</div>
    <div class="abs foot-rule" style="left:133px;top:1136px;width:150px"></div>
    <ul class="abs foot-list links" style="left:133px;top:1151px">
      <li>Copmany</li><li>Technical Services</li><li>Creative Services</li><li>Partners</li><li>&nbsp;Contact Us</li>
    </ul>

    <div class="abs foot-head" style="left:313px;top:1114px">Contact</div>
    <div class="abs foot-rule" style="left:313px;top:1136px;width:150px"></div>
    <ul class="abs foot-list" style="left:313px;top:1152px;line-height:20px">
      <li style="height:20px">UK: +555018273</li><li style="height:20px">USA: +555026491</li><li>text@infolane-example.com</li>
    </ul>

    <div class="abs foot-head" style="left:494px;top:1113px">Follow Us</div>
    <div class="abs foot-rule" style="left:494px;top:1136px;width:145px"></div>
    <div class="abs" style="left:495px;top:1150px">
      <div class="soc"><i></i>FRIENDWALL</div>
      <div class="soc"><i style="background:#5ab4d8"></i>CHIRPLINE</div>
      <div class="soc"><i style="background:#3a6ea5"></i>WORKLINK</div>
    </div>

    <div class="abs foot-head" style="left:715px;top:1113px">Graphic Designers</div>
    <div class="abs foot-rule" style="left:715px;top:1136px;width:148px"></div>
    <ul class="abs foot-list links" style="left:715px;top:1151px">
      <li>Print</li><li>Logo Design</li><li>Website Design</li><li>Illustration</li>
    </ul>

    <div class="abs foot-divider"></div>
    <div class="abs foot-brand"><i></i><span>47VORA</span></div>
  </footer>

  <section class="abs gd">
    <div class="gd-cell" style="width:231px">
      <div class="gd-title">Print</div>
      <div class="gd-art" role="img" aria-label="Illustration of an advertising billboard" style="background:linear-gradient(135deg,#f08a8a,#c0392b)"></div>
      <div class="more">More</div>
    </div>
    <div class="gd-cell" style="width:228px">
      <div class="gd-title">Logo Design</div>
      <div class="gd-art" role="img" aria-label="Illustration of a round emblem" style="background:linear-gradient(135deg,#ff8a3d,#c62d0c)"></div>
      <div class="more">More</div>
    </div>
    <div class="gd-cell" style="width:246px">
      <div class="gd-title">Web Design</div>
      <div class="gd-art" role="img" aria-label="Illustration of brushes and pencils in a glass" style="background:linear-gradient(135deg,#bfe5ff,#6aa6d8)"></div>
      <div class="more">More</div>
    </div>
    <div class="gd-cell" style="width:246px">
      <div class="gd-title">Illustration</div>
      <div class="gd-art" role="img" aria-label="Illustration of a takeout box with chopsticks" style="background:linear-gradient(135deg,#e9f7c9,#9bbd5a)"></div>
      <div class="more">More</div>
    </div>
  </section>

</div>
</body>
</html>
```